BrivoNest Learning App for Children with Dyslexia

Project Description:

We are seeking a talented UI/UX designer to create engaging and intuitive designs for Brivonest, an innovative educational app designed to help children learn letters and words through a multisensory learning approach. The app aims to be particularly helpful for children with dyslexia, providing a supportive and interactive learning environment.

Key App Features & Design Requirements:

Account Creation Screen: Design a welcoming and straightforward sign-up page that allows users to register with their email or continue with Quarnix. The design should be clean, focusing on user-friendliness and accessibility, adhering to our terms of service and privacy policy.

Main Screen Design: The main screen should allocate at least 4/6 of its height to the interactive drawing area. It needs to display word prompts in both correct and scrambled orders and include options to "Show all Words," "Play all words," and a search function. The interface should be vibrant, engaging, and easy to navigate for children.

Profile Section: Create a user-friendly profile page that allows users to edit their profile image, name, username, email, links, and bio. The design should be clean and encourage user engagement.

BrivoTally Page: This section will display the user's learning progress, including rankings, a learning curve, and recently learned words. It should visually represent progress in a motivating and understandable way, suitable for a younger audience.

Visual and Auditory Feedback Implementation: Incorporate elements that support visual and auditory feedback, using dyslexia-friendly formats. This includes choosing appropriate colors, fonts, and auditory cues.

Accessibility and Customization Settings: Designs should include settings for adjusting visual contrast, font size, and the word list to accommodate individual preferences and needs.

Feel free to add more interactions and/or pages.

Design preferences:

Color Scheme: Use a bright, inviting color palette that stimulates learning and engagement without overwhelming the users.
Font Selection: Opt for fonts that are readable and accessible, particularly for users with dyslexia.
Icons and Graphics: Design custom icons and graphics that are cohesive with the app's theme and purpose. Illustrations should be simple, relatable, and supportive of the learning process.

Target Market(s)

Educational

Industry/Entity Type

Educational

Colors
0054AA
0677BA
7BADD7
CADEEF
E8F1F8
0094D4
00A9DD
6FCCEA
C7EBF8
E9F6FB

Requirements
Must have
• Educational app, a writing area, scoring and account management
Nice to have
• Statistics, Ranking Page, Settings and some nice visual features

```html
<!DOCTYPE html>
<html lang="en">
<head>
<meta charset="utf-8">
<title>BrivoNest – App Screens</title>
<link href="https://fonts.googleapis.com/css2?family=Poppins:wght@400;500;600;700;800;900&display=swap" rel="stylesheet">
<style>
  :root{
    --navy:#0054AA;
    --blue:#0677BA;
    --sky:#0094D4;
    --cyan:#00A9DD;
    --cyan-soft:#6FCCEA;
    --ice:#C7EBF8;
    --mist:#E9F6FB;
    --pale:#E8F1F8;
    --ink:#2b2b33;
    --muted:#6b6f78;
    --line:#e3e8ee;
    --white:#ffffff;
  }
  *{box-sizing:border-box;margin:0;padding:0}
  html,body{width:1200px;height:1056px;overflow:hidden}
  body{background:var(--sky);font-family:'Poppins',sans-serif;color:var(--ink);position:relative}
  .screen{position:absolute;top:101px;width:294px;height:638px;border-radius:32px;overflow:hidden;
    background:linear-gradient(180deg,#e4eef8 0%,#f3f7fb 55%,#f7f4ef 100%)}
  .screen--signup{left:86px}
  .screen--home{left:449px}
  .screen--profile{left:811px}
  .abs{position:absolute}
  .center{left:0;right:0;text-align:center}

  /* sign up */
  .brand{font-weight:700;font-size:19px;letter-spacing:.3px;color:#333}
  .tagline{font-size:12px;color:#444}
  .heading{font-weight:800;font-size:19.5px;color:#333}
  .sub{font-size:12.5px;line-height:18px;color:#444}
  .field{left:18px;width:258px;top:181px;height:39px;border:1.5px solid var(--cyan);border-radius:20px;background:var(--white)}
  .field__label{position:absolute;left:26px;top:-10px;background:#eaf1f8;padding:0 3px;font-size:11.5px;color:#333}
  .field__hint{position:absolute;left:30px;top:11px;font-size:10.5px;color:#c9cfd6}
  .field__icon{position:absolute;right:5px;top:5px;width:28px;height:28px;border-radius:50%;background:var(--cyan-soft)}
  .btn{left:18px;width:258px;height:39px;border-radius:20px;background:var(--blue);color:var(--white);
    font-weight:700;font-size:12px;display:flex;align-items:center;justify-content:center;letter-spacing:.1px}
  .divider-text{top:296px;font-size:12.5px;color:#444}
  .divider-line{top:306px;height:1px;width:66px;background:var(--cyan-soft)}
  .btn-alt{left:18px;width:258px;top:331px;height:36px;border-radius:19px;background:var(--white);
    border:1px solid #e6eaef;display:flex;align-items:center;justify-content:center;gap:10px;
    font-weight:600;font-size:12px;color:#333}
  .btn-alt__dot{width:14px;height:14px;border-radius:50%;border:3px solid var(--blue)}
  .legal{top:383px;font-size:11px;line-height:17px;color:#555}
  .illustration{background:radial-gradient(circle at 55% 55%,#f3c7c2 0%,#e9eef3 55%,#f3f1ec 100%);border-radius:14px}

  /* home */
  .topbar-title{top:21px;font-weight:700;font-size:15px;color:#333}
  .menu{left:13px;top:26px;width:15px}
  .menu span{display:block;height:2px;background:#333;margin-bottom:4px;border-radius:1px}
  .points{left:218px;top:24px;width:64px;height:17px;border-radius:9px;background:var(--cyan);
    color:var(--white);font-size:9.5px;display:flex;align-items:center;justify-content:center}
  .canvas-area{left:13px;top:61px;width:269px;height:221px;background:var(--white);border-radius:6px;border:1px solid #e6ecf2}
  .toggle{left:13px;top:303px;width:269px;height:39px;border:1.5px solid var(--cyan);border-radius:20px;background:var(--white);display:flex;overflow:hidden}
  .toggle__opt{flex:1;display:flex;align-items:center;justify-content:center;font-weight:700;font-size:9.5px;color:#333}
  .toggle__opt--on{background:var(--cyan);color:var(--white);border-radius:20px}
  .word{width:84px;height:93px;background:var(--white);border-radius:6px;box-shadow:0 1px 3px rgba(0,0,0,.06);
    display:flex;flex-direction:column;align-items:center;justify-content:flex-end;padding-bottom:12px;font-weight:500;font-size:12.5px}
  .word__icon{width:40px;height:40px;border-radius:10px;margin-bottom:10px}
  .results{top:580px}

  /* profile */
  .back{left:18px;top:24px}
  .page-title{top:21px;font-weight:600;font-size:15.5px;color:#333}
  .card{left:14px;top:95px;width:268px;height:543px;background:var(--white);border-radius:6px 6px 0 0}
  .avatar{left:110px;top:66px;width:76px;height:76px;border-radius:50%;background:linear-gradient(135deg,#8fd0b0,#f2b76a)}
  .edit{top:156px;font-weight:500;font-size:12.5px;color:var(--blue);display:flex;justify-content:center;align-items:center;gap:6px}
  .row-label{left:31px;font-size:12px;color:#333}
  .row-value{right:57px;font-size:12px;color:#333;text-align:right}
  .chev{right:32px}
  .rule{left:14px;width:268px;height:1px;background:var(--line)}
  .add-link{right:57px;top:385px;font-weight:500;font-size:12.5px;color:var(--blue)}

  /* footer message */
  .thanks{left:0;right:0;text-align:center;color:#f2f6fa;font-weight:900;letter-spacing:1px;line-height:1}
  .thanks--one{top:838px;font-size:78px}
  .thanks--two{top:922px;font-size:78px}
</style>
</head>
<body>

<section class="screen screen--signup" aria-label="Create account screen">
  <div class="abs center brand" style="top:29px">BRIVONEST</div>
  <div class="abs center tagline" style="top:57px">Learn letters and words</div>
  <div class="abs center heading" style="top:95px">CREATE AN ACCOUNT</div>
  <div class="abs center sub" style="top:126px">Enter your email to sign up<br>for this app</div>
  <div class="abs field">
    <span class="field__label">Email</span>
    <span class="field__hint">email@domain.com</span>
    <span class="field__icon"><svg width="28" height="28" viewBox="0 0 28 28"><rect x="9" y="10" width="10" height="8" rx="1" fill="#fff"/><path d="M9 11 L14 15 L19 11" stroke="#6FCCEA" stroke-width="1.2" fill="none"/></svg></span>
  </div>
  <div class="abs btn" style="top:242px">SIGN UP WITH EMAIL</div>
  <div class="abs divider-line" style="left:18px"></div>
  <div class="abs divider-line" style="left:210px"></div>
  <div class="abs center divider-text">or continue with</div>
  <div class="abs btn-alt"><span class="btn-alt__dot"></span>QUARNIX</div>
  <div class="abs center legal">By clicking continue, you agree to our and<br>Terms of Service Privacy Policy</div>
  <div class="abs illustration" role="img" aria-label="Illustration of a child beside a tablet with an apple and ABC blocks" style="left:41px;top:450px;width:219px;height:188px"></div>
</section>

<section class="screen screen--home" aria-label="Main drawing screen">
  <div class="abs menu"><span></span><span></span><span></span></div>
  <div class="abs center topbar-title">BRIVONEST</div>
  <div class="abs points">16 Points</div>
  <div class="abs canvas-area" aria-label="Drawing area"></div>
  <div class="abs toggle">
    <div class="toggle__opt">SHOW ALL WORDS</div>
    <div class="toggle__opt toggle__opt--on">PLAY ALL WORDS</div>
  </div>
  <div class="abs word" style="left:13px;top:362px"><span class="word__icon" role="img" aria-label="Number blocks icon" style="background:linear-gradient(135deg,#f26b6b,#f5a13b)"></span>Word 1</div>
  <div class="abs word" style="left:105px;top:362px"><span class="word__icon" role="img" aria-label="Shape blocks icon" style="background:linear-gradient(135deg,#e83e5a,#1d8fd1)"></span>Word 2</div>
  <div class="abs word" style="left:198px;top:362px"><span class="word__icon" role="img" aria-label="Letter balloon icon" style="background:linear-gradient(135deg,#ffb52e,#f28a1a);border-radius:50%"></span>Word 3</div>
  <div class="abs word" style="left:13px;top:462px"><span class="word__icon" role="img" aria-label="Letter wheel icon" style="background:linear-gradient(135deg,#8a4a1f,#4caf50);border-radius:50%"></span>Word 4</div>
  <div class="abs word" style="left:105px;top:462px"><span class="word__icon" role="img" aria-label="Stacked letter blocks icon" style="background:linear-gradient(135deg,#ef5a5a,#45c0d8)"></span>Word 5</div>
  <div class="abs word" style="left:198px;top:462px"><span class="word__icon" role="img" aria-label="Books and blocks icon" style="background:linear-gradient(135deg,#8bd36a,#1e88e5)"></span>Word 6</div>
  <div class="abs btn results">SHOW ME THE RESULTS</div>
</section>

<section class="screen screen--profile" aria-label="Profile screen">
  <svg class="abs back" width="10" height="16" viewBox="0 0 10 16"><path d="M8 2 L2 8 L8 14" stroke="#333" stroke-width="2" fill="none" stroke-linecap="round"/></svg>
  <div class="abs center page-title">PROFILE</div>
  <div class="abs card"></div>
  <div class="abs avatar" role="img" aria-label="Profile picture"></div>
  <div class="abs center edit"><svg width="13" height="13" viewBox="0 0 13 13"><path d="M2 11 L2.6 8.4 L8.6 2.4 L10.6 4.4 L4.6 10.4 Z" fill="none" stroke="#0677BA" stroke-width="1.5"/></svg>Edit profile image</div>

  <div class="abs row-label" style="top:195px">Name</div>
  <div class="abs row-value" style="top:195px">Mira Dalton</div>
  <div class="abs rule" style="top:223px"></div>
  <div class="abs row-label" style="top:237px">Username</div>
  <div class="abs row-value" style="top:237px">@username</div>
  <div class="abs rule" style="top:266px"></div>
  <div class="abs row-label" style="top:279px">Email</div>
  <div class="abs row-value" style="top:279px">name@brivomail.com</div>
  <div class="abs rule" style="top:309px"></div>
  <div class="abs row-label" style="top:323px">Links</div>
  <div class="abs row-value" style="top:323px;line-height:21px">kidspage.net<br>mypage.net<br>ourpage.net</div>
  <div class="abs add-link">+ Add link</div>
  <div class="abs rule" style="top:422px"></div>
  <div class="abs row-label" style="top:433px">Bio</div>
  <div class="abs row-value" style="top:433px">A description of this user.</div>
  <div class="abs rule" style="top:465px"></div>

  <svg class="abs chev" style="top:198px" width="8" height="13" viewBox="0 0 8 13"><path d="M1.5 1.5 L6.5 6.5 L1.5 11.5" stroke="#333" stroke-width="1.6" fill="none"/></svg>
  <svg class="abs chev" style="top:240px" width="8" height="13" viewBox="0 0 8 13"><path d="M1.5 1.5 L6.5 6.5 L1.5 11.5" stroke="#333" stroke-width="1.6" fill="none"/></svg>
  <svg class="abs chev" style="top:282px" width="8" height="13" viewBox="0 0 8 13"><path d="M1.5 1.5 L6.5 6.5 L1.5 11.5" stroke="#333" stroke-width="1.6" fill="none"/></svg>
  <svg class="abs chev" style="top:326px" width="8" height="13" viewBox="0 0 8 13"><path d="M1.5 1.5 L6.5 6.5 L1.5 11.5" stroke="#333" stroke-width="1.6" fill="none"/></svg>
  <svg class="abs chev" style="top:436px" width="8" height="13" viewBox="0 0 8 13"><path d="M1.5 1.5 L6.5 6.5 L1.5 11.5" stroke="#333" stroke-width="1.6" fill="none"/></svg>

  <div class="abs illustration" role="img" aria-label="Illustration of a child beside a tablet with an apple and ABC blocks" style="left:80px;top:496px;width:150px;height:131px"></div>
</section>

<div class="abs thanks thanks--one">THANKS</div>
<div class="abs thanks thanks--two">FOR WATCHING</div>

</body>
</html>
```